Health Care Company with Logo Needs Business Cards designed

We are a luxury behavioral health company looking for business cards design we already have a logo and are looking for someone to design a sophisticated luxurious looking business card. Please note that Card design should be captivating just like the logo and also encompass the logo color

Industry/Entity Type

Healthcare

Contact Information for Business Card

Logo,company name, tagline, my name and title, contact details, and physical address

```html
<!DOCTYPE html>
<html lang="en">
<head>
<meta charset="utf-8">
<title>Marlow Behavioral Health – Business Cards</title>
<link rel="stylesheet" href="https://fonts.googleapis.com/css2?family=Roboto+Condensed:wght@700&family=Roboto:ital,wght@0,400;0,500;1,400&display=swap">
<style>
  :root {
    --backdrop: #2b2b2b;
    --card: #efefef;
    --purple: #6f2c86;
    --blue: #0f86c7;
    --grad-top: #6d3a8b;
    --grad-bottom: #0e7fc0;
    --text: #3a3a3a;
    --muted: #4a4a4a;
  }
  html, body {
    margin: 0; padding: 0;
    width: 1200px; height: 1138px;
    overflow: hidden;
    background: var(--backdrop);
  }
  .card {
    position: absolute;
    background: var(--card);
    border-radius: 14px;
    overflow: hidden;
  }
  .card--front { left: 274px; top: 186px; width: 623px; height: 376px; }
  .card--back  { left: 276px; top: 607px; width: 618px; height: 375px; }

  .brand-name {
    font-family: "Roboto Condensed", "Arial Narrow", sans-serif;
    font-weight: 700;
    color: var(--purple);
    margin: 0;
    white-space: nowrap;
  }
  .tagline {
    font-family: "Roboto Condensed", "Arial Narrow", sans-serif;
    font-weight: 700;
    color: var(--blue);
    text-transform: uppercase;
    margin: 0;
    white-space: nowrap;
  }

  /* front */
  .front-lockup {
    position: absolute; left: 0; right: 0; top: 146px;
    text-align: center;
  }
  .front-lockup .brand-name { font-size: 44px; line-height: 50px; }
  .front-lockup .tagline { font-size: 13.5px; letter-spacing: 3.6px; margin-top: 2px; }

  /* back */
  .back-panel { position: absolute; left: 0; top: 0; }
  .back-mark {
    position: absolute; left: 24px; top: 168px; width: 200px;
    text-align: center;
    font-family: "Roboto Condensed", "Arial Narrow", sans-serif;
    font-weight: 700; font-size: 42px; color: #ffffff;
  }
  .back-info {
    position: absolute; right: 26px; top: 34px;
    text-align: right;
  }
  .back-info .brand-name { font-size: 29px; line-height: 32px; }
  .back-info .tagline { font-size: 9.5px; letter-spacing: 1.9px; margin-top: 2px; }
  .person-name {
    font-family: "Roboto", Arial, sans-serif; font-weight: 500;
    font-size: 22px; color: var(--purple); margin: 52px 0 0; line-height: 26px;
  }
  .person-title {
    font-family: "Roboto", Arial, sans-serif; font-style: italic;
    font-size: 14.5px; color: var(--text); margin: 2px 0 0;
  }
  .address {
    font-family: "Roboto", Arial, sans-serif; font-size: 14px;
    color: var(--muted); line-height: 22px; margin: 22px 0 0; font-style: normal;
  }
  .contacts { list-style: none; padding: 0; margin: 8px 0 0; }
  .contacts li {
    font-family: "Roboto", Arial, sans-serif; font-size: 14px; color: var(--muted);
    line-height: 22px; display: flex; justify-content: flex-end; align-items: center; gap: 12px;
  }
  .contacts svg { width: 14px; height: 14px; flex: none; }
</style>
</head>
<body>

<section class="card card--front">
  <div class="front-lockup">
    <h1 class="brand-name">Marlow Behavioral Health</h1>
    <p class="tagline">Dedicated to hope, healing and recovery</p>
  </div>
</section>

<section class="card card--back">
  <svg class="back-panel" width="618" height="375" viewBox="0 0 618 375">
    <defs>
      <linearGradient id="panelGrad" x1="0" y1="0" x2="0.35" y2="1">
        <stop offset="0" stop-color="var(--grad-top)"/>
        <stop offset="1" stop-color="var(--grad-bottom)"/>
      </linearGradient>
    </defs>
    <circle cx="12" cy="196" r="276" fill="var(--purple)"/>
    <circle cx="20" cy="189" r="271" fill="#1a9be0"/>
    <circle cx="18" cy="190" r="268" fill="url(#panelGrad)"/>
  </svg>
  <div class="back-mark">Marlow</div>

  <div class="back-info">
    <h2 class="brand-name">Marlow Behavioral Health</h2>
    <p class="tagline">Dedicated to hope, healing and recovery</p>
    <p class="person-name">DANIEL REEVE</p>
    <p class="person-title">Managing Director</p>
    <address class="address">123, Anywhere ST, Any City,<br>Any Town, US 123456</address>
    <ul class="contacts">
      <li>000-111-0000
        <svg viewBox="0 0 14 14"><path d="M2 5c0-2 2-3 5-3s5 1 5 3v1H9V5H5v1H2z M3 7h8l1 5H2z" fill="var(--purple)"/><circle cx="7" cy="9.5" r="1.5" fill="#fff"/></svg>
      </li>
      <li>daniel@marlowbehavioral.com
        <svg viewBox="0 0 14 14"><rect x="1" y="3" width="12" height="8" fill="var(--purple)"/><path d="M1 3l6 5 6-5" stroke="#fff" fill="none" stroke-width="1"/></svg>
      </li>
      <li>www.marlowbehavioral.com
        <svg viewBox="0 0 14 14"><circle cx="7" cy="7" r="5.5" fill="var(--blue)"/><path d="M1.5 7h11M7 1.5v11M3 4h8M3 10h8" stroke="#fff" stroke-width="0.7" fill="none"/><ellipse cx="7" cy="7" rx="2.5" ry="5.5" stroke="#fff" stroke-width="0.7" fill="none"/></svg>
      </li>
    </ul>
  </div>
</section>

</body>
</html>
```